Menu Design Project

Menu design for a Japanese fast food restaurant featuring Teppanyaki and Sushi. The restaurant main scene color is black and wood color. No Japan scenery pictures. Menu try to be simply and elegant . Pictures provided can be used accordingly to the menu items, but doesn't have to be due to the back ground color of the picture is white.

Target Market(s)

Young and progressive consumers

Industry/Entity Type

Asian Restaurant

Font styles to use
Other font styles liked:
• Han Wang Kan Tan Font

Colors
1b1b1b
fee18a

Requirements
Must have
• Pictures of the Sushi that is provided, and all the item in the Word file.
Nice to have
• Keep it simple but different
Should not have
• No scenery pictures, no cherry blossom.

```html
<!DOCTYPE html>
<html lang="en">
<head>
<meta charset="utf-8">
<title>Sushi Menu – Tri-fold</title>
<link rel="stylesheet" href="https://fonts.googleapis.com/css2?family=Anton&family=PT+Sans:wght@400;700&display=swap">
<style>
  :root{
    --ink:#1b1b1b;
    --panel:#141414;
    --gold:#fee18a;
    --gold-deep:#c9a650;
    --gold-mid:#e9cd78;
    --paper:#f4f4f4;
    --muted:#d9d9d9;
    --stage:#c9c9c9;
    --note:#4a4a4a;
  }
  *{box-sizing:border-box;margin:0;padding:0}
  html,body{width:1200px;height:800px;overflow:hidden}
  body{background:radial-gradient(ellipse at 50% 45%,#f0f0f0 0%,var(--stage) 100%);font-family:"PT Sans",sans-serif;color:var(--paper);position:relative}

  .menu{position:absolute;left:30px;top:40px;width:1140px;height:720px;display:flex}
  .panel{position:relative;width:380px;height:720px;background:var(--panel);overflow:hidden}
  .panel + .panel{border-left:1px solid #2a2a2a}

  .corner{position:absolute;display:block}
  .gold-fill{fill:url(#goldGrad)}

  .band{position:relative;background:linear-gradient(90deg,var(--gold-deep),var(--gold) 55%,var(--gold-mid));color:var(--ink);font-family:"Anton",sans-serif;text-transform:uppercase;letter-spacing:.5px;line-height:1;padding:6px 0}
  .band--left{clip-path:polygon(0 0,100% 0,94% 100%,0 100%);padding-left:0;text-align:center;font-size:24px;margin-right:18px}
  .band--center{clip-path:polygon(4% 0,96% 0,100% 100%,0 100%);text-align:center;font-size:26px}
  .band--maki{clip-path:polygon(0 0,100% 0,96% 100%,0 100%);text-align:center;font-size:22px;margin-right:30px}

  .photo{border-radius:4px;flex:none}
  .photo--tempura{background:radial-gradient(circle,#f3c95a 0%,#d99a2b 60%,transparent 72%)}
  .photo--fish{background:linear-gradient(90deg,#f7a88a,#e9566c 40%,#f6d6cc 70%,#f7e6c9)}
  .photo--handroll{background:linear-gradient(160deg,#e89a5a,#3c4a2c 55%,#1d251a)}
  .photo--roll{background:linear-gradient(90deg,#e9e3d3,#7fae4a 35%,#f08a6a 65%,#efe9dc)}

  /* Left panel */
  .left{padding:58px 18px 0 18px}
  .price-list{display:flex;justify-content:space-between;margin:10px 0 8px}
  .items{display:flex;flex-direction:column;gap:4px}
  .item-name{font-weight:700;font-size:13px;text-transform:uppercase;line-height:1.05}
  .item-desc{font-size:10.5px;color:var(--muted);line-height:1.15}
  .prices{font-weight:700;font-size:11.5px;text-align:right;line-height:1.55}
  .appetizer-grid{display:grid;grid-template-columns:1fr 76px 48px;gap:0 6px;margin:10px 0 8px;align-items:start}
  .appetizer-grid .items{grid-column:1}
  .appetizer-grid .photo{grid-column:2;width:74px;height:70px;margin-top:30px}
  .appetizer-grid .prices{grid-column:3}
  .spacer{height:14px}
  .section-row{display:flex;align-items:center;gap:8px;margin:8px 0 8px}
  .section-row .list{flex:1;font-size:10.5px;line-height:1.25}
  .section-row .side{display:flex;flex-direction:column;align-items:flex-end;gap:3px;font-size:10px}
  .photo--sashimi{width:130px;height:34px}
  .photo--nigiri{width:110px;height:34px}
  .build .list{font-size:10.5px;line-height:1.2}
  .build .pick{font-weight:700;font-size:12px;text-transform:uppercase}
  .photo--handroll{width:56px;height:74px}

  /* Middle panel */
  .center{padding:0 16px}
  .center .band--center{margin:12px 0 0}
  .availability{text-align:center;font-size:12px;margin:6px 0 4px}
  .group-title{font-weight:700;font-size:16px;text-transform:uppercase;line-height:1}
  .roll{display:grid;grid-template-columns:1fr 52px 46px;gap:0 4px;align-items:center;margin-top:3px}
  .roll .item-name{font-size:12.5px}
  .roll .item-desc{font-size:10px}
  .roll .photo{width:50px;height:18px}
  .roll .prices{font-size:11px}
  .maki{margin-top:10px}
  .maki-row{display:grid;grid-template-columns:1fr auto;align-items:end;margin-top:4px}
  .maki-row .prices{font-size:10px}

  /* Right panel */
  .right{padding:0 16px}
  .photo--top{position:absolute;right:16px;top:20px;width:230px;height:60px}
  .right-list{position:absolute;left:18px;right:16px;top:108px}
  .right-row{display:grid;grid-template-columns:1fr 82px;gap:0 6px;align-items:start;margin-bottom:5px}
  .right-row .prices{font-size:10px;line-height:1.3}
  .photo--small{width:30px;height:32px;justify-self:end}
  .warning{margin-top:8px;background:var(--note);padding:6px 10px;text-align:center;font-size:9.5px;line-height:1.2;color:var(--muted)}
  .warning strong{display:block;color:var(--gold);font-size:11px;text-transform:uppercase}
  .photo--bottom{position:absolute;right:40px;bottom:24px;width:170px;height:170px;border-radius:18px;background:linear-gradient(160deg,#f3f1ec 0%,#f29c7d 30%,#f5efe0 50%,#a7c259 70%,#ecebe6 100%)}
</style>
</head>
<body>
<svg width="0" height="0" style="position:absolute" aria-hidden="true">
  <defs>
    <linearGradient id="goldGrad" x1="0" y1="0" x2="1" y2="1">
      <stop offset="0" stop-color="#c9a650"/>
      <stop offset=".55" stop-color="#fee18a"/>
      <stop offset="1" stop-color="#d8b862"/>
    </linearGradient>
  </defs>
</svg>

<main class="menu">
  <!-- Left panel -->
  <section class="panel left">
    <svg class="corner" style="left:0;top:0" width="380" height="60" aria-hidden="true"><polygon class="gold-fill" points="0,0 380,0 380,8 0,50"/></svg>
    <svg class="corner" style="left:0;bottom:0" width="380" height="60" aria-hidden="true"><polygon class="gold-fill" points="0,60 0,30 380,0 380,60"/></svg>

    <h2 class="band band--left">Appetizer</h2>
    <div class="appetizer-grid">
      <div class="items">
        <div><div class="item-name">Seaweed Salad</div><div class="item-desc">seasoned seaweed</div></div>
        <div><div class="item-name">Kani Salad Spicy or Non-Spicy</div><div class="item-desc">crab meat, cucumber, lettuce with dressing</div></div>
        <div><div class="item-name">Tempura Shrimp</div><div class="item-desc">4 Pieces Fried Tempura Shrimp</div></div>
        <div class="spacer"></div>
        <div class="item-name">Fried Gyoza (6pcs)</div>
        <div class="item-name">Spring Roll (4pcs)</div>
        <div class="item-name">Crab Rangoon (5pcs)</div>
      </div>
      <div class="photo photo--tempura" role="img" aria-label="Photo of fried tempura shrimp"></div>
      <div class="prices">$2.99<br>$3.99<br><br>$5.99<br><br><br>$3.99<br>$2.59<br>$4.50</div>
    </div>

    <h2 class="band band--left">Sashimi</h2>
    <div class="section-row">
      <p class="list">*Salmon, *Tuna, *Yellow Tail,<br>*Red Snapper, *White Tuna,<br>Surf Clam</p>
      <div class="photo photo--sashimi" role="img" aria-label="Photo of assorted sashimi slices"></div>
    </div>

    <h2 class="band band--left">Sushi Nigiri</h2>
    <div class="section-row">
      <p class="list">*Salmon, *Tuna, *Yellow Tail,<br>*Red Snapper, *White Tuna,<br>Surf Clam, Grill Eel, Ebi Shrimp,<br>Kani crab meat</p>
      <div class="side">
        <div class="photo photo--nigiri" role="img" aria-label="Photo of assorted nigiri sushi"></div>
        <span>5 pieces for <b>$5.99</b></span>
      </div>
    </div>

    <h2 class="band band--left">Hand Roll Build Your Own:</h2>
    <div class="section-row build">
      <div class="list">
        <div class="pick">Pick one protein:</div>
        <p>*Salmon, *Tuna, *Yellow Tail, *Red Snapper, *White Tuna, Surf Clam, Grill Eel, Ebi Shrimp, Kani crab meat</p>
        <div class="pick">Pick two vegetable:</div>
        <p>Cucumber, Avocado, Lettuce, Oshigo, Asparagus, Seaweed</p>
        <div class="pick">Pick sauce:</div>
        <p>Spicy Mayonnaise, Honey Wasabi, Honey Mayonnaise, Unagi Sauce</p>
      </div>
      <div class="side">
        <div class="photo photo--handroll" role="img" aria-label="Photo of a hand roll cone"></div>
        <span>2 for <b>$5.99</b></span>
      </div>
    </div>
  </section>

  <!-- Middle panel -->
  <section class="panel center">
    <h2 class="band band--center">Sushi</h2>
    <p class="availability">Ingredients subject to availability</p>
    <h3 class="group-title">Special Roll</h3>

    <div class="roll"><div><div class="item-name">Dragon Roll</div><div class="item-desc">Grilled Eel fish &amp; cucumber top with avocado &amp; Unagi sauce</div></div><div class="photo photo--roll" role="img" aria-label="Photo of dragon roll"></div><div class="prices">$9.99</div></div>
    <div class="roll"><div><div class="item-name">Deluxe Black Dragon Roll</div><div class="item-desc">Tempura Shrimp top with Avocado, Grilled Eel fish &amp; Unagi sauce</div></div><div class="photo photo--roll" role="img" aria-label="Photo of black dragon roll"></div><div class="prices">$11.99</div></div>
    <div class="roll"><div><div class="item-name">*Rainbow Roll</div><div class="item-desc">avocado, cucumber &amp; Kani top with red snapper, tuna, salmon &amp; avocado</div></div><div class="photo photo--roll" role="img" aria-label="Photo of rainbow roll"></div><div class="prices">$10.99</div></div>
    <div class="roll"><div><div class="item-name">*Four Season Roll</div><div class="item-desc">Tuna, salmon, oshinko</div></div><div></div><div class="prices">$9.99</div></div>
    <div class="roll"><div><div class="item-name">*Deluxe Philly Roll</div><div class="item-desc">Salmon, cream cheese &amp; avocado top with more salmon</div></div><div></div><div class="prices">$9.9</div></div>
    <div class="roll"><div><div class="item-name">*Massago Roll</div><div class="item-desc">Kani crab meat, cucumber &amp; avocado top with Premium Massago Roe</div></div><div class="photo photo--roll" role="img" aria-label="Photo of massago roll"></div><div class="prices">$8.99</div></div>
    <div class="roll"><div><div class="item-name">*Deluxe Spicy Tuna Roll</div><div class="item-desc">Kani crab meat, Cucumber &amp; avocado top with Spicy grounded tuna</div></div><div class="photo photo--roll" role="img" aria-label="Photo of spicy tuna roll"></div><div class="prices">$9.49</div></div>
    <div class="roll"><div><div class="item-name">Deluxe Spicy Kani Roll</div><div class="item-desc">Kani crab meat, cucumber &amp; avocado top with seasoned ground Crab meat</div></div><div class="photo photo--roll" role="img" aria-label="Photo of spicy kani roll"></div><div class="prices">$9.49</div></div>
    <div class="roll"><div><div class="item-name">Deluxe Kani Roll</div><div class="item-desc">Kani crab meat, cucumber &amp; avocado top with Kani &amp; Panko crumb</div></div><div></div><div class="prices">$9.49</div></div>
    <div class="roll"><div><div class="item-name">*Tri Deluxe Fish Roll</div><div class="item-desc">Tuna, salmon &amp; red snapper</div></div><div></div><div class="prices">$9.99</div></div>
    <div class="roll"><div><div class="item-name">*Sumo Roll</div><div class="item-desc">Tuna, Salmon, White Tuan, Red snapper Avocado &amp; Kani Crab Meat</div></div><div></div><div class="prices">$10.99</div></div>
    <div class="roll"><div><div class="item-name">*Hamachi Asparagus Roll</div><div class="item-desc">Hamachi, Scallion &amp; Asparagus with Ponzu Sauce</div></div><div></div><div class="prices">$7.99</div></div>

    <div class="maki">
      <h2 class="band band--maki">Regular Maki Roll</h2>
      <div class="maki-row"><div><div class="item-name">*Salmon Roll</div><div class="item-desc">salmon &amp; avocado</div></div><div class="prices">(8pcs) $5.49 (12pcs) $7.49</div></div>
      <div class="maki-row"><div><div class="item-name">*Tuna Roll</div><div class="item-desc">tuna &amp; avocado</div></div><div class="prices">(8pcs) $5.49 (12pcs) $7.49</div></div>
      <div class="maki-row"><div><div class="item-name">*Philly Roll</div><div class="item-desc">salmon, cream cheese &amp; avocado</div></div><div class="prices">(8pcs) $5.49 (12pcs) $7.49</div></div>
    </div>
  </section>

  <!-- Right panel -->
  <section class="panel right">
    <svg class="corner" style="right:0;top:0" width="300" height="100" aria-hidden="true"><polygon class="gold-fill" points="20,0 300,0 300,100 200,100"/></svg>
    <div class="photo photo--top" role="img" aria-label="Photo of tuna, white fish and salmon nigiri"></div>

    <div class="right-list">
      <div class="right-row"><div><div class="item-name">California Roll</div><div class="item-desc">cucumber, avocado &amp; kani crab meat</div></div><div class="prices">(8pcs) $5.49<br>(12pcs) $7.49</div></div>
      <div class="right-row"><div><div class="item-name">Kani &amp; Cheese Roll</div><div class="item-desc">Kani crab meat &amp; cream cheese</div></div><div class="prices">(8pcs) $5.49<br>(12pcs) $7.49</div></div>
      <div class="right-row"><div><div class="item-name">Shrimp Tempura Roll</div><div class="item-desc">Fried tempura shrimp &amp; cucumber</div></div><div class="prices">(8pcs) $6.49</div></div>
      <div class="right-row"><div><div class="item-name">*Alaska Roll</div><div class="item-desc">Salmon &amp; avocado with massago</div></div><div class="photo photo--small photo--roll" role="img" aria-label="Photo of alaska roll piece"></div></div>
      <div class="right-row"><div><div class="item-name">Grilled Eel Roll</div><div class="item-desc">Eel &amp; avocado</div></div><div class="prices">(8pcs) $5.49<br>(12pcs) $7.49</div></div>
      <div class="right-row"><div><div class="item-name">*Spicy Tuna Roll</div><div class="item-desc">seasoned ground tuna</div></div><div class="prices">(8pcs) $5.49<br>(12pcs) $7.49</div></div>
      <div class="right-row"><div><div class="item-name">*Spicy Salmon Roll</div><div class="item-desc">seasoned ground salmon</div></div><div class="prices">(8pcs) $5.49<br>(12pcs) $7.49</div></div>
      <div class="right-row"><div><div class="item-name">*Spicy Kani Roll</div><div class="item-desc">seasoned ground crab meat</div></div><div class="prices">(8pcs) $5.49<br>(12pcs) $7.49</div></div>
      <div class="right-row"><div><div class="item-name">Vegetarian Roll</div><div class="item-desc">avocado, cucumber<br>Add Ajitsuke seasoned fried bean curd</div></div><div class="prices">(8pcs) $4.49<br>(16pcs) $7.99<br>for $1.00 more</div></div>
      <div class="warning"><strong>*Items may be served raw or under cooked</strong>consuming raw or undercooked meat, poultry, shellfish, eggs or seafood may increase your risk of food borne illness.</div>
    </div>

    <svg class="corner" style="left:0;bottom:0" width="380" height="240" aria-hidden="true"><polygon class="gold-fill" points="120,0 380,40 380,240 0,240 0,200"/></svg>
    <div class="photo photo--bottom" role="img" aria-label="Close-up photo of a salmon, cream cheese and avocado roll"></div>
  </section>
</main>
</body>
</html>
```